New Brand - Website Design (4 Pages)

We are launching a new brand for electronic cigarettes. We already have logo and packaging done and would like a web design to go with it.

We are interested in the following deliverables:

1) Home Page Design
2) Check Out Design
3) How it Works Page
4) Secondary Template Page Design

Looking for a 60s modern look and something that is consistent with our logo and packaging.

Industry/Entity Type

Electronic

Requirements
Must have
• Consistent with logo and packaging (Use Logo Attached)
White background

Example (Functionality & Design): http://www.moltrafen.co.uk/
Example (Design): http://www.brendolark.com/

We want the design more like brendolark but the functionality the same as moltrafen.

Top Bar: Pale Dunes Kits; Cartridge Refills; How it Works; Contact; My Account; Checkout
Should not have
• Stock List or Search Bar or Newsletter Signup

```html
<!DOCTYPE html>
<html lang="en">
<head>
<meta charset="utf-8">
<title>Pale Dunes Kits</title>
<link rel="stylesheet" href="https://fonts.googleapis.com/css2?family=Open+Sans:wght@400;600;700&display=swap">
<style>
  :root {
    --red: #b9372b;
    --red-dark: #96281e;
    --ink: #2b2b2b;
    --muted: #6b6b6b;
    --line: #dcdcdc;
    --sky-light: #f1f5f9;
    --sky: #c8d8e7;
    --frame: #8cc0e4;
    --panel: #ececec;
    --footer: #2a2a2a;
    --footer-text: #bdbdbd;
    --white: #ffffff;
  }
  * { margin: 0; padding: 0; box-sizing: border-box; }
  html, body { width: 824px; height: 1200px; overflow: hidden; background: var(--white); }
  body { font-family: "Open Sans", Arial, sans-serif; color: var(--ink); position: relative; }

  .site-header { position: absolute; top: 0; left: 0; width: 824px; height: 88px; }
  .brand { position: absolute; left: 58px; top: 18px; display: flex; align-items: center; gap: 10px; }
  .brand-dot { width: 46px; height: 46px; border-radius: 50%; background: var(--ink); }
  .brand-name { font-size: 26px; font-weight: 700; letter-spacing: 2px; color: var(--ink); text-transform: uppercase; }
  .account-links { position: absolute; right: 60px; top: 10px; display: flex; gap: 22px; font-size: 10px; color: var(--muted); }
  .main-nav { position: absolute; right: 56px; top: 44px; display: flex; gap: 6px; font-size: 11px; font-weight: 600; }
  .main-nav a { color: var(--ink); text-decoration: none; padding: 6px 10px; border-radius: 12px; }
  .main-nav a.is-active { background: var(--sky); border: 1px solid var(--frame); }

  .hero { position: absolute; top: 88px; left: 0; width: 824px; height: 337px;
    background: radial-gradient(ellipse at 50% 40%, var(--sky-light) 0%, var(--sky) 100%); overflow: hidden; }
  .hero-product { position: absolute; left: 140px; top: 18px; width: 220px; height: 240px;
    background: linear-gradient(160deg, #3a3a3a 0%, #1b1b1b 55%, #c2482a 100%); }
  .hero-copy { position: absolute; left: 452px; top: 52px; width: 270px; }
  .hero-copy h1 { font-size: 16px; font-weight: 700; margin-bottom: 10px; }
  .hero-copy p { font-size: 10px; line-height: 1.5; color: var(--muted); }
  .btn-shop { display: inline-block; margin-top: 18px; background: #151515; color: var(--white);
    font-size: 13px; font-weight: 700; padding: 9px 28px; border-radius: 4px; }
  .hero-arrow { position: absolute; top: 150px; width: 22px; height: 30px; background: #333; }
  .hero-arrow.prev { left: 0; } .hero-arrow.next { right: 0; }
  .hero-arrow svg { display: block; margin: 9px auto; }
  .hero-wave { position: absolute; bottom: 0; left: 0; }
  .hero-dots { position: absolute; bottom: 22px; left: 50%; transform: translateX(-50%); display: flex; gap: 6px; }
  .hero-dots span { width: 7px; height: 7px; border-radius: 50%; background: #9aaab8; }
  .hero-dots span.on { background: var(--ink); }

  .features { position: absolute; top: 440px; left: 55px; display: flex; gap: 30px; }
  .feature { width: 220px; }
  .feature h2 { font-size: 15px; font-weight: 600; color: var(--red); padding-bottom: 4px;
    border-bottom: 1px solid var(--line); margin-bottom: 8px; }
  .feature-media { width: 220px; height: 118px; border: 2px solid var(--frame); border-radius: 4px;
    background: linear-gradient(135deg, #f6f6f6, #d9d9d9); }
  .feature .lead { font-size: 10px; font-weight: 700; margin: 8px 0 3px; }
  .feature p { font-size: 9px; line-height: 1.45; color: var(--muted); }
  .btn-more { display: block; width: 48px; margin: 6px 0 0 auto; background: var(--red); color: var(--white);
    font-size: 9px; font-weight: 700; text-align: center; padding: 4px 0; border-radius: 2px; }

  .welcome { position: absolute; top: 785px; left: 48px; width: 728px; height: 160px;
    background: var(--panel); border-radius: 8px; padding: 14px 18px; }
  .welcome h2 { font-size: 17px; font-weight: 600; color: var(--ink); padding-bottom: 6px; border-bottom: 1px solid var(--line); }
  .welcome h2 span { color: var(--red); }
  .welcome-body { display: flex; gap: 16px; margin-top: 12px; }
  .welcome-media { width: 130px; height: 88px; flex: none; border-radius: 3px;
    background: linear-gradient(90deg, #8fd0e8, #d18fd8, #b8e08a); }
  .welcome-body .lead { font-size: 10px; font-weight: 700; margin-bottom: 4px; }
  .welcome-body p { font-size: 9px; line-height: 1.5; color: var(--muted); }

  .products { position: absolute; top: 960px; left: 48px; width: 728px; }
  .products-head { display: flex; justify-content: space-between; align-items: center;
    border-bottom: 1px solid var(--line); padding-bottom: 4px; }
  .products-head h2 { font-size: 17px; font-weight: 600; }
  .products-head h2 span { color: var(--red); }
  .products-nav { display: flex; gap: 4px; }
  .product-list { display: flex; gap: 28px; margin-top: 10px; padding: 0 8px; }
  .product { width: 220px; }
  .product-media { height: 52px; border: 1px solid var(--line);
    background: linear-gradient(135deg, #fafafa, #e0e0e0); }
  .product p { font-size: 9px; line-height: 1.4; color: var(--muted); margin: 5px 0; }
  .product-foot { display: flex; justify-content: space-between; align-items: center; }
  .price { font-size: 13px; font-weight: 700; color: var(--red); }
  .btn-details { background: var(--red); color: var(--white); font-size: 9px; font-weight: 700;
    padding: 4px 12px; border-radius: 2px; text-transform: uppercase; }

  .site-footer { position: absolute; top: 1112px; left: 0; width: 824px; height: 88px; background: var(--footer); }
  .social { position: absolute; left: 60px; top: 20px; display: flex; gap: 5px; }
  .social span { width: 16px; height: 16px; border-radius: 2px; background: #555; }
  .footer-info { position: absolute; right: 60px; top: 22px; text-align: right; font-size: 9px; line-height: 1.7; color: var(--footer-text); }
</style>
</head>
<body>
  <header class="site-header">
    <div class="brand"><span class="brand-dot"></span><span class="brand-name">Pale Dunes</span></div>
    <div class="account-links"><span>My Account</span><span>Check Out</span></div>
    <nav class="main-nav">
      <a class="is-active">Pale Dunes Kits</a>
      <a>Cartridge Refills</a>
      <a>How it Works</a>
      <a>Contact</a>
    </nav>
  </header>

  <section class="hero">
    <div class="hero-product" role="img" aria-label="Product box of the starter kit"></div>
    <div class="hero-copy">
      <h1>Lorem Ipsum Dolor Sit Amet, Elit</h1>
      <p>Cum sociis natoque penatibus et magnis dis parturient montes, nascetur ridiculus mus. In iaculis facilisis massa. Etiam eu urna. Sed porta nunc luctus tempus.</p>
      <span class="btn-shop">Shop Now</span>
    </div>
    <div class="hero-arrow prev"><svg width="8" height="12" viewBox="0 0 8 12"><path d="M7 1 2 6l5 5" fill="none" stroke="#fff" stroke-width="2"/></svg></div>
    <div class="hero-arrow next"><svg width="8" height="12" viewBox="0 0 8 12"><path d="M1 1l5 5-5 5" fill="none" stroke="#fff" stroke-width="2"/></svg></div>
    <svg class="hero-wave" width="824" height="60" viewBox="0 0 824 60"><path d="M0 40 Q412 -10 824 40 L824 60 L0 60Z" fill="#fff"/></svg>
    <div class="hero-dots"><span class="on"></span><span></span><span></span></div>
  </section>

  <section class="features">
    <article class="feature">
      <h2>Getbox</h2>
      <div class="feature-media" role="img" aria-label="Starter kit box"></div>
      <p class="lead">Mauris vel lacus vitae felis vestibulum volutpat.</p>
      <p>Sed ut perspiciatis unde omnis iste natus error sit voluptatem accusantium doloremque laudantium, totam rem aperiam eaque ipsa.</p>
      <span class="btn-more">More</span>
    </article>
    <article class="feature">
      <h2>Customizer</h2>
      <div class="feature-media" role="img" aria-label="Customised kit packaging"></div>
      <p class="lead">Mauris vel lacus vitae felis vestibulum volutpat.</p>
      <p>Sed ut perspiciatis unde omnis iste natus error sit voluptatem accusantium doloremque laudantium, totam rem aperiam eaque ipsa.</p>
      <span class="btn-more">More</span>
    </article>
    <article class="feature">
      <h2>How it Works</h2>
      <div class="feature-media" role="img" aria-label="Electronic cigarette parts"></div>
      <p class="lead">Mauris vel lacus vitae felis vestibulum volutpat.</p>
      <p>Sed ut perspiciatis unde omnis iste natus error sit voluptatem accusantium doloremque laudantium, totam rem aperiam eaque ipsa.</p>
      <span class="btn-more">More</span>
    </article>
  </section>

  <section class="welcome">
    <h2>Welcome to <span>Pale Dunes Kits</span></h2>
    <div class="welcome-body">
      <div class="welcome-media" role="img" aria-label="Coloured refill cartridges"></div>
      <div>
        <p class="lead">Mauris vel lacus vitae felis vestibulum volutpat. Etiam est nunc, venenatis.</p>
        <p>Sed ut perspiciatis unde omnis iste natus error sit voluptatem accusantium doloremque laudantium, totam rem aperiam, eaque ipsa quae ab illo inventore veritatis et quasi architecto beatae vitae dicta sunt explicabo. Nemo enim ipsam voluptatem quia voluptas sit aspernatur aut odit aut fugit.</p>
      </div>
    </div>
  </section>

  <section class="products">
    <div class="products-head">
      <h2>Our <span>Products</span></h2>
      <div class="products-nav">
        <svg width="8" height="10" viewBox="0 0 8 10"><path d="M7 0v10L0 5z" fill="#2b2b2b"/></svg>
        <svg width="8" height="10" viewBox="0 0 8 10"><path d="M1 0v10l7-5z" fill="#2b2b2b"/></svg>
      </div>
    </div>
    <div class="product-list">
      <div class="product">
        <div class="product-media" role="img" aria-label="Set of electronic cigarettes"></div>
        <p>Lorem ipsum dolor sit amet, nostrud exercitation ullamco laboris nisi.</p>
        <div class="product-foot"><span class="price">$52.65</span><span class="btn-details">Details</span></div>
      </div>
      <div class="product">
        <div class="product-media" role="img" aria-label="Boxed starter kit"></div>
        <p>Lorem ipsum dolor sit amet, nostrud exercitation ullamco laboris nisi.</p>
        <div class="product-foot"><span class="price">$52.65</span><span class="btn-details">Details</span></div>
      </div>
      <div class="product">
        <div class="product-media" role="img" aria-label="Refill cartridge pack"></div>
        <p>Lorem ipsum dolor sit amet, nostrud exercitation ullamco laboris nisi.</p>
        <div class="product-foot"><span class="price">$52.65</span><span class="btn-details">Details</span></div>
      </div>
    </div>
  </section>

  <footer class="site-footer">
    <div class="social"><span></span><span></span><span></span><span></span><span></span></div>
    <div class="footer-info">
      <div>Pale Dunes Kits, Cartridge Refills, How it Works, Contact</div>
      <div>© 2013. Pale Dunes Kits. All Rights Reserved</div>
    </div>
  </footer>
</body>
</html>
```